Brightmill Data Works

Our company is about IT hardwares and IT solutions. IT hardware such as PC, RAMS, storage and servers. IT solutions such as project management, BA. We are also selling new technology too.

Target Market(s)

Consumer, Small to Medium Business, Corporate

Requirements
Must have
• The business card must have the following:
• Name:
• Title:
• Contact Number:
• Email address:
• Website:
• Color: Must match the logo color upgrade

```html
<!DOCTYPE html>
<html lang="en">
<head>
<meta charset="utf-8">
<title>Brightmill Data Works — Business Card</title>
<link rel="stylesheet" href="https://fonts.googleapis.com/css2?family=Exo+2:wght@400;600;700&display=swap">
<style>
  :root {
    --backdrop: #d8d8d6;
    --slate-dark: #4f4f50;
    --slate-light: #6e6e6f;
    --amber: #d9893f;
    --amber-light: #e0a24c;
    --amber-deep: #d4883a;
    --paper: #f3f3f2;
    --ink: #4a4a4c;
    --white: #ffffff;
  }
  * { box-sizing: border-box; margin: 0; padding: 0; }
  html, body {
    width: 1200px; height: 864px; overflow: hidden;
    background: var(--backdrop);
    font-family: "Exo 2", sans-serif;
  }
  .canvas {
    position: relative; width: 1200px; height: 864px;
  }
  .card {
    position: absolute; width: 600px; height: 343px;
    border-radius: 4px; overflow: hidden;
    box-shadow: 0 10px 24px rgba(0,0,0,0.18);
  }
  .card-front { left: 300px; top: 470px; }
  .card-back { left: 300px; top: 60px;
    background: linear-gradient(160deg, var(--amber-light), var(--amber-deep)); }
  .card-shapes { position: absolute; inset: 0; }

  .holder { position: absolute; left: 58px; top: 50px; }
  .holder-name {
    color: var(--white); font-size: 21px; font-weight: 600;
    letter-spacing: 1.5px; text-transform: uppercase;
  }
  .holder-title {
    color: var(--amber); font-size: 16px; font-weight: 400;
    letter-spacing: 1.5px; text-transform: uppercase; margin-top: 2px;
  }
  .contacts { position: absolute; left: 58px; top: 212px; list-style: none; }
  .contact {
    display: flex; align-items: center; gap: 10px;
    color: var(--white); font-size: 15px; letter-spacing: 1px;
    margin-bottom: 8px;
  }
  .contact-icon {
    width: 18px; height: 18px; border-radius: 2px;
    background: var(--amber); display: flex; align-items: center; justify-content: center;
  }
  .brand-name {
    position: absolute; color: var(--ink);
    font-weight: 700; text-transform: uppercase; line-height: 1.05;
    text-align: center;
  }
  .card-front .brand-name { left: 370px; top: 185px; width: 220px; font-size: 27px; letter-spacing: 1px; }
  .card-back .brand-name { left: 330px; top: 228px; width: 240px; font-size: 29px; letter-spacing: 1px; }
</style>
</head>
<body>
<main class="canvas">

  <section class="card card-back" aria-label="Card back">
    <p class="brand-name">Brightmill<br>Data Works</p>
  </section>

  <section class="card card-front" aria-label="Card front">
    <svg class="card-shapes" viewBox="0 0 600 343" width="600" height="343" aria-hidden="true">
      <defs>
        <linearGradient id="slateFill" x1="0" y1="0" x2="1" y2="1">
          <stop offset="0" stop-color="#4e4e4f"/>
          <stop offset="1" stop-color="#737374"/>
        </linearGradient>
        <linearGradient id="amberFill" x1="0" y1="0" x2="1" y2="1">
          <stop offset="0" stop-color="#d08a4e"/>
          <stop offset="1" stop-color="#de8a35"/>
        </linearGradient>
      </defs>
      <rect width="600" height="343" fill="url(#slateFill)"/>
      <path d="M272,0 C236,120 252,262 330,343 L600,343 L600,0 Z" fill="url(#amberFill)"/>
      <path d="M600,48 C470,46 388,104 376,175 C366,250 398,308 448,343 L600,343 Z" fill="var(--paper)"/>
      <path d="M330,128 C392,70 470,52 545,48 C470,60 398,86 342,140 Z" fill="var(--paper)"/>
    </svg>

    <div class="holder">
      <p class="holder-name">Dana Whitlow</p>
      <p class="holder-title">Manager</p>
    </div>

    <ul class="contacts">
      <li class="contact">
        <span class="contact-icon">
          <svg width="12" height="12" viewBox="0 0 12 12" aria-hidden="true"><path d="M2.5,1 L4.5,1 L5.3,3.5 L4,4.6 C4.6,6 6,7.4 7.4,8 L8.5,6.7 L11,7.5 L11,9.5 C11,10.3 10.3,11 9.5,11 C5,11 1,7 1,2.5 C1,1.7 1.7,1 2.5,1 Z" fill="#fff"/></svg>
        </span>+1-555-014-2290
      </li>
      <li class="contact">
        <span class="contact-icon">
          <svg width="12" height="10" viewBox="0 0 12 10" aria-hidden="true"><rect x="0.6" y="0.6" width="10.8" height="8.8" fill="none" stroke="#fff" stroke-width="1.2"/><path d="M0.6,0.8 L6,5.5 L11.4,0.8" fill="none" stroke="#fff" stroke-width="1.2"/></svg>
        </span>dana@brightmilldata.com
      </li>
      <li class="contact">
        <span class="contact-icon">
          <svg width="12" height="12" viewBox="0 0 12 12" aria-hidden="true"><g fill="none" stroke="#fff" stroke-width="1"><circle cx="6" cy="6" r="5"/><ellipse cx="6" cy="6" rx="2.2" ry="5"/><path d="M1,6 H11 M2,3.2 H10 M2,8.8 H10"/></g></svg>
        </span>www.brightmilldata.com
      </li>
    </ul>

    <p class="brand-name">Brightmill<br>Data Works</p>
  </section>

</main>
</body>
</html>
```